Birchline Septic Solutions

Would like to see some single sided ones but would also like to see some double sided with one sided only being the logo. Owners name is Colin Vandro. Phone number is 555-214-0387
Services are pumping, inspections, installs, and repairs

Contact Information for Business Card

555-241-0387 Colin Vandro Cedar Hollow, OH

```html
<!DOCTYPE html>
<html lang="en">
<head>
<meta charset="utf-8">
<title>Birchline Septic Solutions – Business Cards</title>
<link href="https://fonts.googleapis.com/css2?family=Montserrat:wght@400;500;800&display=swap" rel="stylesheet">
<style>
  :root {
    --bg: #3a3a3a;
    --ink: #111111;
    --paper: #ffffff;
    --teal: #35beb8;
    --muted: #2a2a2a;
  }
  * { margin: 0; padding: 0; box-sizing: border-box; }
  html, body { width: 1200px; height: 960px; overflow: hidden; background: var(--bg); }
  body { font-family: "Montserrat", sans-serif; position: relative; }

  .card {
    position: absolute; left: 250px; width: 700px; height: 400px;
    border-radius: 22px; overflow: hidden;
  }
  .card--back { top: 50px; background: var(--ink); color: var(--paper); }
  .card--front { top: 510px; background: var(--paper); color: var(--ink); }

  .wordmark { display: flex; align-items: center; gap: 14px; font-weight: 800; }
  .wordmark__square { width: 22px; height: 22px; background: var(--teal); flex: none; }
  .wordmark__text { line-height: 1; }
  .wordmark__name { display: block; font-size: 54px; letter-spacing: 1px; }
  .wordmark__tag { display: block; font-size: 17px; letter-spacing: 7px; margin-top: 8px; }

  .card--back .wordmark { position: absolute; left: 120px; top: 105px; }
  .services {
    position: absolute; left: 0; right: 0; top: 260px; text-align: center;
    font-size: 21px; font-weight: 400; line-height: 1.45;
  }
  .tick { display: inline-block; width: 17px; height: 17px; vertical-align: -2px; margin-right: 6px; }

  .front-bands { position: absolute; left: 0; top: 0; width: 700px; height: 400px; }

  .card--front .wordmark { position: absolute; left: 36px; top: 150px; color: var(--ink); }
  .card--front .wordmark__name { font-size: 40px; }
  .card--front .wordmark__tag { font-size: 13px; letter-spacing: 5px; }
  .divider { position: absolute; left: 376px; top: 78px; width: 2px; height: 150px; background: var(--teal); }

  .contact { position: absolute; left: 396px; top: 78px; white-space: nowrap; }
  .contact__name { font-size: 28px; font-weight: 800; letter-spacing: -0.5px; }
  .contact__name span { color: var(--teal); }
  .contact__role { font-size: 15px; font-weight: 500; color: var(--muted); margin-top: 2px; }
  .contact__list { list-style: none; margin-top: 16px; font-size: 15px; font-weight: 500; }
  .contact__list li { display: flex; align-items: center; gap: 10px; margin-bottom: 8px; }
  .contact__list svg { width: 18px; height: 18px; flex: none; }
</style>
</head>
<body>

<section class="card card--back" aria-label="Business card back">
  <div class="wordmark">
    <span class="wordmark__square"></span>
    <span class="wordmark__text">
      <span class="wordmark__name">BIRCHLINE</span>
      <span class="wordmark__tag">SEPTIC SOLUTIONS</span>
    </span>
  </div>
  <p class="services">
    <svg class="tick" viewBox="0 0 20 20"><circle cx="10" cy="10" r="8.5" fill="none" stroke="#fff" stroke-width="2"/><path d="M6 10.5l3 3 5-6" fill="none" stroke="#fff" stroke-width="2"/></svg>Services are pumping<br>
    <svg class="tick" viewBox="0 0 20 20"><circle cx="10" cy="10" r="8.5" fill="none" stroke="#fff" stroke-width="2"/><path d="M6 10.5l3 3 5-6" fill="none" stroke="#fff" stroke-width="2"/></svg>inspections
    <svg class="tick" viewBox="0 0 20 20"><circle cx="10" cy="10" r="8.5" fill="none" stroke="#fff" stroke-width="2"/><path d="M6 10.5l3 3 5-6" fill="none" stroke="#fff" stroke-width="2"/></svg>installs
    <svg class="tick" viewBox="0 0 20 20"><circle cx="10" cy="10" r="8.5" fill="none" stroke="#fff" stroke-width="2"/><path d="M6 10.5l3 3 5-6" fill="none" stroke="#fff" stroke-width="2"/></svg>and repairs
  </p>
</section>

<section class="card card--front" aria-label="Business card front">
  <svg class="front-bands" viewBox="0 0 700 400" aria-hidden="true">
    <polygon points="0,378 700,378 700,400 0,400" fill="#111"/>
    <polygon points="640,255 700,255 700,400 615,400 615,278 630,268" fill="#111"/>
    <polygon points="450,300 606,300 612,290 458,290" fill="#35beb8"/>
    <polygon points="0,368 190,368 200,358 0,358" fill="#35beb8"/>
    <polygon points="205,358 395,358 405,348 215,348" fill="#111"/>
    <polygon points="410,348 590,348 600,338 420,338" fill="#35beb8"/>
  </svg>
  <div class="wordmark">
    <span class="wordmark__square"></span>
    <span class="wordmark__text">
      <span class="wordmark__name">BIRCHLINE</span>
      <span class="wordmark__tag">SEPTIC SOLUTIONS</span>
    </span>
  </div>
  <div class="divider"></div>
  <div class="contact">
    <p class="contact__name">COLIN <span>VANDRO</span></p>
    <p class="contact__role">Owners</p>
    <ul class="contact__list">
      <li><svg viewBox="0 0 20 20"><path d="M4 3h4l2 4-2.5 1.5a10 10 0 0 0 4 4L13 10l4 2v4a2 2 0 0 1-2 2A14 14 0 0 1 2 5a2 2 0 0 1 2-2z" fill="#35beb8"/></svg>555-214-0387</li>
      <li><svg viewBox="0 0 20 20"><path d="M10 1a6 6 0 0 0-6 6c0 4.5 6 12 6 12s6-7.5 6-12a6 6 0 0 0-6-6zm0 8.5A2.5 2.5 0 1 1 10 4.5a2.5 2.5 0 0 1 0 5z" fill="#35beb8"/></svg>Colin Vandro Cedar Hollow, OH</li>
    </ul>
  </div>
</section>

</body>
</html>
```